Dental Practice Website design

Design a new website for Brambleford Dental Practice.
Design should be warm, neutral in colour, with some small amount of bright colour if needed but kept to a minimum. Website should look professional, high end. Home page should be easy to navigate and simple for patients to be able to book online.
Logo in files along with some examples of websites that we like. Please ask if any further info needed.
Menu should have:
About
New Patients
Treatments
Fees
Contact Us

Industry/Entity Type

Dentistry

Number of Pages Required

4 page

Font styles to use
Sans Serif

Colors

Designer to choose colors to be used in the design.

Requirements
Must have
• Ravelle ratings badge, book online button,
Nice to have
• neutral, relaxing colours
Should not have
• harsh, bright colours!

```html
<!DOCTYPE html>
<html lang="en">
<head>
<meta charset="utf-8">
<title>Brambleford Dental Practice</title>
<link rel="stylesheet" href="https://fonts.googleapis.com/css2?family=Lora:wght@500;600;700&family=Roboto:wght@400;500;700&display=swap">
<style>
:root{
  --teal:#4f8a80;
  --teal-soft:#d6e8e3;
  --ink:#2b2b2b;
  --muted:#5e6462;
  --hero-bg:#e6e7e9;
  --mint:#e3f6ef;
  --line:#d8dcdb;
  --white:#ffffff;
  --map-base:#e9ebee;
  --map-blue:#c9d3e6;
}
*{box-sizing:border-box;margin:0;padding:0}
html,body{width:1200px;height:4088px;overflow:hidden}
body{font-family:"Roboto",Arial,sans-serif;color:var(--ink);background:var(--white);position:relative}
.btn{display:inline-block;background:var(--teal);color:var(--white);font-size:13px;font-weight:700;text-transform:uppercase;padding:10px 22px;border-radius:20px;text-decoration:none;letter-spacing:.3px;white-space:nowrap}
.btn-light{background:var(--white);color:var(--ink);border:1px solid var(--line)}
.img-fill{display:block}

.topbar{height:32px;background:var(--teal);color:var(--white);font-size:12px;display:flex;justify-content:flex-end;align-items:center;gap:26px;padding-right:120px}
.topbar span{display:flex;align-items:center;gap:6px}

.header{height:80px;display:flex;align-items:center;padding:0 120px;justify-content:space-between}
.logo{display:flex;align-items:center;gap:10px}
.logo-mark{width:22px;height:22px;background:var(--teal)}
.logo-name{font-family:"Lora",Georgia,serif;font-weight:600;font-size:17px;color:var(--ink);width:150px;line-height:1.15}
.nav{display:flex;align-items:center;gap:34px;font-size:14px}
.nav a{color:var(--ink);text-decoration:none}
.nav a.active{color:var(--teal);border-bottom:2px solid var(--teal);padding-bottom:4px}

.hero{position:absolute;top:112px;left:0;width:1200px;height:608px;background:var(--hero-bg)}
.hero-photo{position:absolute;right:0;top:0;width:560px;height:608px;background:linear-gradient(100deg,#e6e7e9 0%,#d8d3cf 30%,#c9b6a6 60%,#a98b73 100%)}
.hero-copy{position:absolute;left:104px;top:162px;width:470px}
.hero-copy h1{font-family:"Lora",Georgia,serif;font-size:40px;line-height:1.2;font-weight:700;text-transform:uppercase}
.hero-copy p{margin-top:18px;font-size:15px;line-height:1.4;color:var(--muted)}
.hero-actions{margin-top:26px;display:flex;gap:12px}
.rating-badge{margin-top:34px;width:180px;height:72px;background:var(--teal-soft);border:2px solid var(--teal);border-radius:10px}

.section-title{position:absolute;left:0;width:1200px;text-align:center;font-family:"Lora",Georgia,serif;font-size:34px;font-weight:600;color:var(--teal);text-transform:uppercase}

.service-img{position:absolute}
.service-text{position:absolute;padding:28px 0 0 30px;border-left:3px solid var(--teal);border-top:3px solid var(--teal)}
.service-text h3{font-family:"Lora",Georgia,serif;font-size:24px;line-height:1.25;font-weight:600;color:var(--teal);text-transform:uppercase}
.service-text p{margin:20px 0 24px;font-size:14px;line-height:1.55;color:var(--muted)}

.about{position:absolute;top:1660px;left:0;width:1200px;height:500px;background:var(--teal)}
.about-photo{position:absolute;left:0;top:0;width:600px;height:500px;background:linear-gradient(90deg,#d9dcde 0%,#b8bfc4 45%,#6f7d8a 100%)}
.about-card{position:absolute;left:572px;top:80px;width:568px;height:360px;background:var(--white);padding:36px 36px}
.about-card h2{font-family:"Lora",Georgia,serif;font-size:34px;font-weight:600;text-transform:uppercase;border-bottom:2px solid var(--ink);display:inline-block;padding-bottom:4px}
.about-card p{margin-top:18px;font-size:13px;line-height:1.55;color:var(--muted)}

.team{position:absolute;top:2360px;left:108px;display:flex;gap:14px}
.team-card{width:246px;height:328px;border:1px solid var(--line);border-radius:4px;text-align:center;padding-top:24px;box-shadow:0 2px 6px rgba(0,0,0,.06)}
.team-photo{width:100px;height:100px;margin:0 auto;background:linear-gradient(180deg,#d5d9dc,#8d969d)}
.team-card h4{margin-top:14px;font-family:"Lora",Georgia,serif;font-size:20px;font-weight:600;color:var(--teal)}
.team-card .role{margin-top:4px;font-size:13px;font-weight:500}
.team-card p{margin:12px auto 20px;width:190px;font-size:12px;line-height:1.45;color:var(--muted)}

.join{position:absolute;top:2768px;left:0;width:1200px;height:292px;background:var(--teal);color:var(--white);text-align:center;padding-top:52px}
.join h2{font-family:"Lora",Georgia,serif;font-size:32px;font-weight:600;text-transform:uppercase}
.join p{width:960px;margin:28px auto 30px;font-size:13px;line-height:1.55}
.join .btn{background:transparent;border:1px solid var(--white)}

.map{position:absolute;top:3060px;left:0;width:1200px;height:560px;
  background:
    radial-gradient(ellipse 420px 260px at 78% 70%,rgba(160,178,210,.55),rgba(160,178,210,0) 70%),
    radial-gradient(ellipse 360px 200px at 20% 30%,rgba(255,255,255,.8),rgba(255,255,255,0) 70%),
    linear-gradient(160deg,#eef0f3 0%,#dfe4ec 50%,var(--map-blue) 100%)}
.contact{position:absolute;top:3472px;left:140px;width:900px;height:430px;display:flex;box-shadow:0 4px 14px rgba(0,0,0,.12)}
.contact-form{width:580px;background:var(--white);padding:24px 24px}
.contact-form h3,.contact-detail h3{font-family:"Lora",Georgia,serif;font-size:28px;font-weight:600;color:var(--teal)}
.contact-form h3{border-bottom:1px solid var(--line);padding-bottom:8px}
.field-row{display:flex;gap:40px;margin-top:30px}
.field{flex:1;font-size:13px;border-bottom:1px solid var(--line);padding-bottom:26px}
.field.tall{padding-bottom:60px}
.contact-detail{width:320px;background:var(--mint)}
.contact-detail h3{background:var(--teal);color:var(--white);padding:14px 20px}
.detail-item{display:flex;gap:10px;padding:14px 20px 0;font-size:12px;line-height:1.5}
.detail-item strong{font-size:14px;display:block}

.footer{position:absolute;top:3920px;left:0;width:1200px;height:168px;border-top:1px solid var(--line)}
.footer .logo{position:absolute;left:140px;top:44px}
.footer-nav{position:absolute;left:416px;top:42px;display:flex;gap:34px;font-size:14px}
.footer-copy{position:absolute;left:416px;top:100px;font-size:12px;color:var(--muted);border-top:1px solid var(--line);padding-top:16px;width:644px}
.social-dot{position:absolute;left:1016px;top:104px;width:30px;height:30px;border-radius:50%;background:var(--teal)}
</style>
</head>
<body>

<div class="topbar">
  <span><svg width="12" height="12" viewBox="0 0 24 24"><path fill="#fff" d="M6.6 10.8a15 15 0 0 0 6.6 6.6l2.2-2.2a1 1 0 0 1 1-.25 11 11 0 0 0 3.6.6 1 1 0 0 1 1 1V20a1 1 0 0 1-1 1A17 17 0 0 1 3 4a1 1 0 0 1 1-1h3.5a1 1 0 0 1 1 1c0 1.25.2 2.45.6 3.6a1 1 0 0 1-.25 1z"/></svg>| Phone Number : +1 555 014 2290</span>
  <span><svg width="10" height="12" viewBox="0 0 20 24"><path fill="#fff" d="M10 0a8 8 0 0 0-8 8c0 6 8 16 8 16s8-10 8-16a8 8 0 0 0-8-8zm0 11a3 3 0 1 1 0-6 3 3 0 0 1 0 6z"/></svg>| Location : Brambleford Dental Practice, Thornbury, UK</span>
</div>

<header class="header">
  <div class="logo"><span class="logo-mark"></span><span class="logo-name">Brambleford Dental Practice</span></div>
  <nav class="nav">
    <a class="active" href="#">Home</a>
    <a href="#">About</a>
    <a href="#">New Patients</a>
    <a href="#">Treatments</a>
    <a href="#">Fees</a>
    <a href="#">Contact Us</a>
    <a class="btn" href="#" style="color:#fff">Book Online</a>
  </nav>
</header>

<section class="hero">
  <div class="hero-photo img-fill" role="img" aria-label="Smiling patient showing healthy white teeth"></div>
  <div class="hero-copy">
    <h1>General and<br>Cosmetic Dentistry</h1>
    <p>Lorem ipsum dolor sit amet, consectetur adipiscing elit, sed do eiusmod tempor incididunt ut labore et dolore magna aliqua.</p>
    <div class="hero-actions"><a class="btn" href="#">Our Treatments</a><a class="btn btn-light" href="#">Book Online</a></div>
    <div class="rating-badge" role="img" aria-label="Ravelle ratings badge"></div>
  </div>
</section>

<h2 class="section-title" style="top:784px">Our Services</h2>

<div class="service-img img-fill" role="img" aria-label="Patient in dental chair receiving a check-up" style="left:192px;top:868px;width:356px;height:320px;background:linear-gradient(120deg,#3f4548,#9aa3a6 50%,#e2e4e4)"></div>
<div class="service-text" style="left:640px;top:880px;width:360px">
  <h3>General and<br>Cosmetic Dentistry</h3>
  <p>Lorem ipsum dolor sit amet, consectetur adipiscing elit, sed do eiusmod tempor incididunt ut labore et dolore magna aliqua. Quis ipsum suspendisse ultrices gravida. Risus commodo viverra maecenas accumsan lacus vel facilisis.</p>
  <a class="btn" href="#">Read More</a>
</div>

<div class="service-text" style="left:200px;top:1272px;width:360px">
  <h3>Orthodontics and<br>Emergency Care</h3>
  <p>Lorem ipsum dolor sit amet, consectetur adipiscing elit, sed do eiusmod tempor incididunt ut labore et dolore magna aliqua. Quis ipsum suspendisse ultrices gravida. Risus commodo viverra maecenas accumsan lacus vel facilisis.</p>
  <a class="btn" href="#">Read More</a>
</div>
<div class="service-img img-fill" role="img" aria-label="Woman holding her jaw with tooth pain" style="left:652px;top:1264px;width:356px;height:316px;background:linear-gradient(120deg,#f1efec,#d9cfc4 50%,#b79d84)"></div>

<section class="about">
  <div class="about-photo img-fill" role="img" aria-label="Dental nurse in blue scrubs standing in the clinic"></div>
  <div class="about-card">
    <h2>About Us</h2>
    <p>Welcome to our friendly dental practice nestled in the heart of beautiful Thornbury, UK. Our team of dedicated dentists, hygienists and support staff are here to provide you with exceptional dental care. With a wide array of services, including general and cosmetic dentistry, orthodontics and emergency care, we're confident that we can deliver the highest quality treatment to you and your loved ones.</p>
    <p>At our practice, we believe that a visit to the dentist should be a comfortable and positive experience.</p>
    <p style="margin-top:24px"><a class="btn" href="#">Read More</a></p>
  </div>
</section>

<h2 class="section-title" style="top:2244px">Our Team</h2>

<div class="team">
  <div class="team-card"><div class="team-photo" role="img" aria-label="Portrait of Dr Oliver"></div><h4>Dr Oliver</h4><div class="role">Principal Dentist &amp; Owner</div><p>Lorem ipsum dolor sit amet, adipiscing, ut labore et dolore magna aliqua.</p><a class="btn" href="#">Book Appointment</a></div>
  <div class="team-card"><div class="team-photo" role="img" aria-label="Portrait of Dr Isabella"></div><h4>Dr Isabella</h4><div class="role">Principal Dentist &amp; Owner</div><p>Lorem ipsum dolor sit amet, adipiscing, ut labore et dolore magna aliqua.</p><a class="btn" href="#">Book Appointment</a></div>
  <div class="team-card"><div class="team-photo" role="img" aria-label="Portrait of Dr William"></div><h4>Dr William</h4><div class="role">Dentist</div><p>Lorem ipsum dolor sit amet, adipiscing, ut labore et dolore magna aliqua.</p><a class="btn" href="#">Book Appointment</a></div>
  <div class="team-card"><div class="team-photo" role="img" aria-label="Portrait of Dr Theodore"></div><h4>Dr Theodore</h4><div class="role">Dentist</div><p>Lorem ipsum dolor sit amet, adipiscing, ut labore et dolore magna aliqua.</p><a class="btn" href="#">Book Appointment</a></div>
</div>

<section class="join">
  <h2>Join Our Practice</h2>
  <p>If you're looking for an exceptional dental practice, we're here to help! Our team is made up of highly skilled professionals who are dedicated to ensuring that all our patients receive top-notch care in a welcoming and comfortable environment. Whether you need a routine examination or a more specialised treatment, we have all the resources to provide you with the best dental care possible. Our practice is always up-to-date with the latest techniques and technologies to make sure that our patients receive the best possible results.</p>
  <a class="btn" href="#">Contact Us</a>
</section>

<div class="map img-fill" role="img" aria-label="Street map showing the practice location in Thornbury"></div>

<section class="contact">
  <div class="contact-form">
    <h3>Contact Us</h3>
    <div class="field-row"><div class="field">Full Name*</div><div class="field">Email*</div></div>
    <div class="field-row"><div class="field">Phone Number*</div><div class="field">Services*</div></div>
    <div class="field-row"><div class="field tall">Message*</div></div>
  </div>
  <div class="contact-detail">
    <h3>Contact Detail</h3>
    <div class="detail-item"><svg width="14" height="18" viewBox="0 0 20 24"><path fill="#4f8a80" d="M10 0a8 8 0 0 0-8 8c0 6 8 16 8 16s8-10 8-16a8 8 0 0 0-8-8zm0 11a3 3 0 1 1 0-6 3 3 0 0 1 0 6z"/></svg><div><strong>Location:</strong>Brambleford Dental Practice, Thornbury, UK</div></div>
    <div class="detail-item"><svg width="16" height="16" viewBox="0 0 24 24"><circle cx="12" cy="12" r="10" fill="none" stroke="#4f8a80" stroke-width="2.5"/><path d="M12 6v6l4 3" stroke="#4f8a80" stroke-width="2.5" fill="none"/></svg><div><strong>Office Hours :</strong>Tuesday 10AM-7PM<br>Thursday 9AM-7PM<br>Saturday 9AM-2PM</div></div>
    <div class="detail-item"><svg width="16" height="16" viewBox="0 0 24 24"><path fill="#4f8a80" d="M6.6 10.8a15 15 0 0 0 6.6 6.6l2.2-2.2a1 1 0 0 1 1-.25 11 11 0 0 0 3.6.6 1 1 0 0 1 1 1V20a1 1 0 0 1-1 1A17 17 0 0 1 3 4a1 1 0 0 1 1-1h3.5a1 1 0 0 1 1 1c0 1.250.2 2.45.6 3.6a1 1 0 0 1-.25 1z"/></svg><div><strong>Number :</strong>Phone: +1 555 014 2290</div></div>
    <div class="detail-item"><svg width="16" height="16" viewBox="0 0 24 24"><rect x="2" y="5" width="20" height="14" fill="none" stroke="#4f8a80" stroke-width="2.2"/><path d="M2 5l10 8 10-8" fill="none" stroke="#4f8a80" stroke-width="2.2"/></svg><div><strong>Email :</strong>hello@bramblefordsmiles.co.uk</div></div>
  </div>
</section>

<footer class="footer">
  <div class="logo"><span class="logo-mark"></span><span class="logo-name">Brambleford Dental Practice</span></div>
  <nav class="footer-nav"><span>Home</span><span>About</span><span>New Patients</span><span>Treatments</span><span>Fees</span><span>Contact Us</span></nav>
  <div class="footer-copy">2025 Brambleford Dental Practice</div>
  <span class="social-dot"></span>
</footer>

</body>
</html>
```